Boutique PEO needs a catchy snail mail and email marketing flyer

Our company provides services to our clients and co-employees throughout the entire life cycle of an employee's employment. It is very serious business to our clients' but we need a catchy message and look to attract the attention of prospective clients. I have attached some of the ideas we tried.

Target Market(s)

small to medium size companies

Font styles to use
Serif

Colors

Designer to choose colors to be used in the design.

```html
<!DOCTYPE html>
<html lang="en">
<head>
<meta charset="utf-8">
<title>PEO Flyers</title>
<link rel="stylesheet" href="https://fonts.googleapis.com/css2?family=Poiret+One&family=Oswald:wght@500;600&display=swap">
<style>
  :root {
    --backdrop: #efe8df;
    --purple-deep: #5a2a7c;
    --purple-mid: #8d4b9f;
    --purple-light: #b86aab;
    --arc-soft: #c586c4;
    --arc-pale: #a65fae;
    --kitten-bg: #040404;
    --kitten-fur: #d9d6d8;
    --chimp-bg: #55524f;
    --chimp-fur: #2e2219;
    --white: #ffffff;
  }
  * { margin: 0; padding: 0; box-sizing: border-box; }
  html, body { width: 1200px; height: 874px; overflow: hidden; }
  body { background: var(--backdrop); position: relative; }

  .flyer {
    position: absolute;
    top: 71px;
    width: 518px;
    height: 731px;
    overflow: hidden;
    box-shadow: 0 2px 8px rgba(0,0,0,0.18);
  }
  .flyer--hanging { left: 70px; }
  .flyer--monkey { left: 613px; }

  .flyer__art { position: absolute; inset: 0; width: 518px; height: 731px; display: block; }

  .flyer__headline {
    position: absolute;
    left: 0; right: 0;
    top: 506px;
    text-align: center;
    color: var(--white);
    font-family: "Poiret One", sans-serif;
    font-size: 25px;
    line-height: 38px;
  }

  .flyer__call {
    position: absolute;
    left: 0; right: 0;
    top: 633px;
    display: flex;
    align-items: center;
    gap: 5px;
    color: var(--white);
    font-family: "Oswald", sans-serif;
    font-weight: 500;
    font-size: 20px;
    line-height: 24px;
  }
  .flyer__call::before,
  .flyer__call::after {
    content: "";
    flex: 1;
    height: 4px;
    background: var(--white);
  }

  .flyer__phone {
    position: absolute;
    left: 0; right: 0;
    top: 660px;
    text-align: center;
    color: var(--white);
    font-family: "Oswald", sans-serif;
    font-weight: 600;
    font-size: 41px;
    line-height: 52px;
  }
</style>
</head>
<body>

  <section class="flyer flyer--hanging">
    <svg class="flyer__art" viewBox="0 0 518 731">
      <defs>
        <linearGradient id="bg-hanging" x1="0.9" y1="0" x2="0.7" y2="1">
          <stop offset="0" stop-color="var(--purple-deep)"/>
          <stop offset="0.6" stop-color="var(--purple-mid)"/>
          <stop offset="1" stop-color="var(--purple-light)"/>
        </linearGradient>
        <radialGradient id="photo-hanging" cx="0.38" cy="0.5" r="0.42">
          <stop offset="0" stop-color="var(--kitten-fur)"/>
          <stop offset="0.45" stop-color="#7d797c"/>
          <stop offset="1" stop-color="var(--kitten-bg)"/>
        </radialGradient>
      </defs>
      <rect width="518" height="731" fill="url(#bg-hanging)"/>
      <path d="M0,0 H395 C478,45 530,130 518,220 V260 C500,350 420,420 310,455 C200,488 90,490 0,486 Z" fill="var(--arc-pale)"/>
      <path d="M0,0 H388 C466,42 514,125 502,210 C488,310 415,390 305,432 C200,470 90,476 0,474 Z" fill="var(--arc-soft)"/>
      <g role="img" aria-label="Photo of a white kitten hanging from a clothesline rope against a black background">
        <path d="M0,0 H382 C455,40 500,120 486,202 C472,300 400,380 300,420 C200,456 90,464 0,462 Z" fill="url(#photo-hanging)"/>
      </g>
    </svg>
    <p class="flyer__headline">HR Issues and Complex Employment<br>Regulations have you hanging?<br>Hold On and</p>
    <p class="flyer__call">CALL A PEO</p>
    <p class="flyer__phone">0300 5550 123 456</p>
  </section>

  <section class="flyer flyer--monkey">
    <svg class="flyer__art" viewBox="0 0 518 731">
      <defs>
        <linearGradient id="bg-monkey" x1="0.9" y1="0" x2="0.7" y2="1">
          <stop offset="0" stop-color="var(--purple-deep)"/>
          <stop offset="0.6" stop-color="var(--purple-mid)"/>
          <stop offset="1" stop-color="var(--purple-light)"/>
        </linearGradient>
        <radialGradient id="photo-monkey" cx="0.5" cy="0.55" r="0.55">
          <stop offset="0" stop-color="#4a3626"/>
          <stop offset="0.5" stop-color="var(--chimp-fur)"/>
          <stop offset="1" stop-color="var(--chimp-bg)"/>
        </radialGradient>
      </defs>
      <rect width="518" height="731" fill="url(#bg-monkey)"/>
      <path d="M0,0 H395 C478,45 530,130 518,220 V260 C500,350 420,420 310,455 C200,488 90,490 0,486 Z" fill="var(--arc-pale)"/>
      <path d="M0,0 H388 C466,42 514,125 502,210 C488,310 415,390 305,432 C200,470 90,476 0,474 Z" fill="var(--arc-soft)"/>
      <g role="img" aria-label="Photo of a thoughtful chimpanzee resting its chin on its hand against a grey background">
        <path d="M0,0 H382 C455,40 500,120 486,202 C472,300 400,380 300,420 C200,456 90,464 0,462 Z" fill="url(#photo-monkey)"/>
      </g>
    </svg>
    <p class="flyer__headline">The Federal Government Does<br>Not Monkey Around When It<br>Comes To Enforcing Regulations</p>
    <p class="flyer__call">CALL A PEO</p>
    <p class="flyer__phone">0300 5550 123 456</p>
  </section>

</body>
</html>
```